Vantro cards

I am in the auto motive, transportation business I would like a business card that is Something cool, modern edgy, having to do with car culture. I offer towing service for high and exotic cars. I also provide towing for collisions and car accidents. I offer open and enclosed transport nationwide.

Target Market(s)

Car culture people high end auto collectors

Industry/Entity Type

Towing car carrier

Contact Information for Business Card

My company colors black yellow and silver

Font styles to use
Serif

```html
<!DOCTYPE html>
<html lang="en">
<head>
<meta charset="utf-8">
<title>Vantro cards</title>
<link rel="stylesheet" href="https://fonts.googleapis.com/css2?family=Poppins:wght@400;600&display=swap">
<style>
  :root {
    --backdrop: #777777;
    --card-white: #ffffff;
    --card-black: #201d1e;
    --ink: #111111;
    --ink-soft: #555555;
    --rule: #c8c8c8;
    --brand-yellow: #f9dc4e;
    --brand-white: #ffffff;
  }
  html, body {
    margin: 0;
    padding: 0;
    width: 1065px;
    height: 1200px;
    overflow: hidden;
    background: var(--backdrop);
    font-family: "Poppins", sans-serif;
  }
  .stage {
    position: relative;
    width: 1065px;
    height: 1200px;
  }
  .card {
    position: absolute;
    width: 583px;
    height: 362px;
    box-sizing: border-box;
  }
  .card--front {
    left: 292px;
    top: 218px;
    background: var(--card-white);
    border-radius: 0 181px 181px 0;
  }
  .card--back {
    left: 263px;
    top: 623px;
    background: var(--card-black);
    border-radius: 181px 0 0 181px;
  }
  .brand {
    position: absolute;
    display: flex;
    align-items: center;
    gap: 8px;
    font-weight: 600;
    line-height: 1;
  }
  .brand__dot {
    display: block;
    background: var(--brand-yellow);
  }
  .card--front .brand {
    left: 40px;
    top: 163px;
    font-size: 30px;
    color: var(--ink);
  }
  .card--front .brand__dot { width: 14px; height: 14px; }
  .card--back .brand {
    left: 50%;
    top: 50%;
    transform: translate(-50%, -50%);
    font-size: 48px;
    color: var(--brand-white);
    gap: 12px;
  }
  .card--back .brand__dot { width: 22px; height: 22px; }
  .divider {
    position: absolute;
    left: 198px;
    top: 95px;
    width: 1px;
    height: 173px;
    background: var(--rule);
  }
  .details {
    position: absolute;
    left: 227px;
    top: 93px;
    color: var(--ink);
  }
  .details__name {
    margin: 0;
    font-size: 21px;
    font-weight: 600;
    line-height: 22px;
    letter-spacing: 0.2px;
  }
  .details__role {
    margin: 0;
    font-size: 16px;
    font-weight: 400;
    line-height: 18px;
    color: var(--ink-soft);
  }
  .contact-list {
    list-style: none;
    margin: 14px 0 0;
    padding: 0;
  }
  .contact-list li {
    display: flex;
    align-items: center;
    gap: 5px;
    font-size: 17px;
    line-height: 21px;
  }
  .contact-list svg {
    width: 15px;
    height: 15px;
    flex: none;
  }
  .address {
    margin: 16px 0 0;
    font-style: normal;
    font-size: 17px;
    line-height: 21px;
  }
</style>
</head>
<body>
<main class="stage">
  <section class="card card--front" aria-label="Card front">
    <div class="brand"><span class="brand__dot"></span>Vantro</div>
    <span class="divider"></span>
    <div class="details">
      <h1 class="details__name">MARCUS HALE</h1>
      <p class="details__role">Managing Director</p>
      <ul class="contact-list">
        <li>
          <svg viewBox="0 0 24 24" aria-hidden="true"><path fill="var(--ink)" d="M6.6 10.8a15 15 0 0 0 6.6 6.6l2.2-2.2c.3-.3.7-.4 1-.2 1.1.4 2.3.6 3.6.6.6 0 1 .4 1 1V20c0 .6-.4 1-1 1A17 17 0 0 1 3 4c0-.6.4-1 1-1h3.5c.6 0 1 .4 1 1 0 1.3.2 2.5.6 3.6.1.3 0 .7-.2 1z"/></svg>
          071-482 530 916
        </li>
        <li>
          <svg viewBox="0 0 24 24" aria-hidden="true"><path fill="var(--ink)" d="M2 5h20v14H2z"/><path fill="none" stroke="var(--card-white)" stroke-width="1.6" d="M2 5l10 8 10-8"/></svg>
          hello@vantrotow.com
        </li>
        <li>
          <svg viewBox="0 0 24 24" aria-hidden="true"><g fill="none" stroke="var(--ink)" stroke-width="2"><circle cx="12" cy="12" r="10"/><ellipse cx="12" cy="12" rx="4.5" ry="10"/><path d="M2 12h20M4 7h16M4 17h16"/></g></svg>
          www.vantrotow.com
        </li>
      </ul>
      <address class="address">88, Harbor Depot Road<br>60318, Eastland</address>
    </div>
  </section>

  <section class="card card--back" aria-label="Card back">
    <div class="brand"><span class="brand__dot"></span>Vantro</div>
  </section>
</main>
</body>
</html>
```